We are a doctors medical practice
I need the business card to be eye catching and memorable,
to reflect professionalism, yet also warmth and care

the numbers need to be easy to see, for the elderly

and the logo also in a location that is large enough to see and be eye catching

Back of card:
opening hours:
Mon- Fri 8.30am to 6pm
Sat 9am to 4pm

rows for appontments, date and time
Updates

HiĀ 

Modification to company name

BROOKVALE KINDRED HEALTH MEDICAL PRACTICE

Thanks
Marla

Reason: I am look for a unique design that also fulfils the design brief

I have attempted to post a .eps and .ai file of the logo

Target Market(s)

needs to appeal to the majority, mainly adults

Industry/Entity Type

Medical

Contact Information for Business Card

company name: Brookvale Kindred Health Medical Practice
Name: Dr Marla Tobrik-Vey
Qualifications: MBBS, BMedSc, FRACGP, DCH, MPH, Dip Paeds
Address: Shop 3/41-43 Corrow St, Fairfield 2165
Ph: 02 9184 3025
Fax: 02 9318 6042

Requirements
Nice to have
• I like balance
gold/ silver incorporated, as well as the other colours in the logo- but not limited to these colours
a "medical" feel
Should not have
• dark or strong colours

```html
<!DOCTYPE html>
<html lang="en">
<head>
<meta charset="utf-8">
<title>Brookvale Kindred Health Medical Practice – Business Card</title>
<link rel="stylesheet" href="https://fonts.googleapis.com/css2?family=Open+Sans:wght@400;600;700&display=swap">
<style>
  :root {
    --page-bg: #e6e6e6;
    --brand-blue: #0a5aa8;
    --brand-olive: #a19a05;
    --ring-blue: #1a8ad4;
    --paper: #ffffff;
    --ink: #222222;
    --dots: #333333;
  }
  * { margin: 0; padding: 0; box-sizing: border-box; }
  html, body {
    width: 1200px; height: 900px; overflow: hidden;
    background: var(--page-bg);
    font-family: "Open Sans", Arial, sans-serif;
  }
  .sheet {
    position: relative; width: 1200px; height: 900px;
    display: flex; align-items: center; justify-content: center; gap: 40px;
  }
  .card {
    position: relative; width: 540px; height: 330px; overflow: hidden;
    background: var(--paper);
    box-shadow: 0 6px 18px rgba(0,0,0,0.18);
  }

  /* Front */
  .card-front { background: var(--brand-blue); color: #fff; }
  .front-shape { position: absolute; inset: 0; }
  .practice-name {
    position: absolute; left: 26px; top: 30px;
    font-size: 14px; font-weight: 600; letter-spacing: 0.2px; line-height: 1.3;
    white-space: nowrap;
  }
  .brand-mark {
    position: absolute; left: 360px; top: 62px; width: 116px; height: 116px;
    border-radius: 50%; background: var(--paper);
    border: 7px solid var(--ring-blue);
    display: flex; align-items: center; justify-content: center; text-align: center;
    color: var(--brand-blue); font-size: 12px; font-weight: 600; line-height: 1.25;
  }
  .doctor { position: absolute; left: 26px; top: 178px; }
  .doctor-name { font-size: 22px; font-weight: 600; line-height: 1.2; }
  .qualifications { font-size: 11px; line-height: 1.35; margin-top: 2px; }
  .contact { margin-top: 12px; font-size: 12.5px; line-height: 1.4; border-collapse: collapse; }
  .contact td { padding: 0; vertical-align: top; }
  .contact .label { width: 58px; }
  .contact .sep { width: 12px; }

  /* Back */
  .hours-band {
    position: absolute; left: 0; top: 0; width: 100%; height: 92px;
    background: var(--brand-blue); color: #fff;
    display: flex; align-items: center; padding: 0 24px; gap: 26px;
  }
  .hours-title { font-size: 21px; font-weight: 600; letter-spacing: 0.3px; }
  .hours-list { font-size: 19px; font-weight: 600; line-height: 1.3; }
  .hours-list span { display: block; }
  .hours-list span + span { padding-left: 24px; }
  .appointments { position: absolute; left: 24px; right: 24px; top: 104px; }
  .appt-head {
    display: flex; justify-content: space-between;
    font-size: 13px; font-weight: 700; color: var(--ink);
  }
  .appt-rows { list-style: none; margin-top: 2px; }
  .appt-rows li { height: 24px; border-bottom: 2px dotted var(--dots); }
</style>
</head>
<body>
<main class="sheet">

  <section class="card card-front" aria-label="Card front">
    <svg class="front-shape" viewBox="0 0 540 330" width="540" height="330" aria-hidden="true">
      <path d="M405,0 C362,110 392,250 470,330 L540,330 L540,0 Z" fill="var(--brand-olive)"/>
      <path d="M405,0 C362,110 392,250 470,330" fill="none" stroke="#ffffff" stroke-width="4"/>
    </svg>
    <h1 class="practice-name">BROOKVALE KINDRED HEALTH MEDICAL PRACTICE</h1>
    <div class="brand-mark">Brookvale<br>Kindred</div>
    <div class="doctor">
      <p class="doctor-name">Dr Marla Tobrik-Vey</p>
      <p class="qualifications">MBBS, BMedSc, FRACGP,<br>DCH, MPH, Dip Paeds</p>
      <table class="contact">
        <tr><td class="label">Tel</td><td class="sep">:</td><td>02 9184 3025</td></tr>
        <tr><td class="label">Fax</td><td class="sep">:</td><td>02 9318 6042</td></tr>
        <tr><td class="label">Address</td><td class="sep">:</td><td>Shop 3/41-43 Corrow St, Kellmore 2318</td></tr>
      </table>
    </div>
  </section>

  <section class="card card-back" aria-label="Card back">
    <div class="hours-band">
      <h2 class="hours-title">OPENING HOURS:</h2>
      <p class="hours-list"><span>Mon- Fri 8.30am to 6pm</span><span>Sat 9am to 4pm</span></p>
    </div>
    <div class="appointments">
      <div class="appt-head"><span>Appontments</span><span>Date &amp; Time</span></div>
      <ul class="appt-rows">
        <li></li><li></li><li></li><li></li><li></li><li></li><li></li><li></li>
      </ul>
    </div>
  </section>

</main>
</body>
</html>
```